Logo and Website Design for QR.KA Horizon - a Software Engineering and IT company

Software engineering and IT are two different disciplines - and yet inseparably linked. At QR.KA Horizon, we combine both worlds and ensure that our software solutions are not only innovative and powerful, but also integrate perfectly into existing IT landscapes. Vision stands more for imagination, so it is not neccessary something what has to do with visualisation. Please consider that the winning competitor is also instructed to make a logo for the company. So please make a suitable logo for QR.KA Horizon to which the website fits to and show it during the website creation process. A good Logo desing is important for winning the competition. The website should contain a landing page with inspiring, perhaps futuristic photos of a datacenter and lines of code. Eventuelly flewent integrated in the text. On the landing page the company should introduced with a small text (max 250 words) followed by a section with a short text to one of our products nearby a graphic visualising the architecture of the product. The menue should be on top and fixed during scrolling and consist of the menue items home, solutions, who are we and a contact button. There should be a footer for linking social media, rights and Impressum. Only as an idea not a must. The very first view on the landing page could also be the menue bar and below of it a transparent unsharp photo (e.g. datacenter, lines of code, both ;) with the company name in the center.

###############################################################

Hi Designers,

Despite your very good approaches for describing QR.KA Horizon, here a short introduction (german text) from ourself:

------
QR.KA Horizon – Ihr Partner für ganzheitliche Softwarelösungen

Die QR.KA Horizon ist ein dynamisches Unternehmen, das sich nicht nur auf die Konzeption, das Design und die Entwicklung maßgeschneiderter Software spezialisiert hat, sondern auch deren reibungslosen Betrieb sicherstellt. Mit einem Team aus erfahrenen Softwarearchitekten und IT-Professionals verbinden wir modernste Softwareentwicklung mit tiefgehendem IT-Know-how – für Lösungen, die nachhaltig, leistungsstark und zukunftssicher sind.

Software Engineering trifft IT – Perfektion in Kombination
Software Engineering und IT sind zwei unterschiedliche Disziplinen – und doch untrennbar miteinander verbunden. Wir bei QR.KA Horizon vereinen beide Welten und sorgen dafür, dass unsere Softwarelösungen nicht nur innovativ und leistungsfähig sind, sondern sich auch perfekt in bestehende IT-Landschaften integrieren.

Expertise mit Fokus auf Healthcare & komplexe IT-Umgebungen
Unsere Experten bringen jahrzehntelange Erfahrung aus dem Healthcare-Sektor mit und unterstützen IT-Abteilungen großer Kliniken in der Entwicklung und Optimierung von Softwarelösungen. Von Anwendungssoftware bis hin zu Steuerungssystemen – unsere Softwareingenieure wissen genau, worauf es ankommt.

Ganzheitlicher Ansatz – über die Software hinaus
Wir entwickeln nicht nur Software, sondern übernehmen auch die Verantwortung für deren stabile und effiziente Betriebsumgebung. Egal, ob on-premises, in der Cloud oder als SaaS-Lösung – wir kümmern uns um den kompletten Lifecycle Ihrer Anwendung.

Ihre Vision – unsere Mission.
Ob Neuentwicklung einer SaaS-Anwendung oder die Migration bestehender Lösungen in eine moderne SaaS-Umgebung – mit QR.KA Horizon haben Sie einen starken Partner an Ihrer Seite.

Lassen Sie uns gemeinsam die Zukunft Ihrer Software gestalten!
--------------

Our first solution called "Clear Record Transfer Gateway" (CLURA)
-------------------
Teilen Sie Ihre Daten sicher – ohne Kompromisse!

Sie nutzen eine relationale Datenbank (Brightcask, Tabulon Hub, Vellumdb etc.) und möchten ausgewählte Daten mit Dritten teilen – sei es für ein Data Warehouse, Business Controller, Lieferanten oder Kunden? Doch dabei sollen Datensicherheit, Integrität und Verfügbarkeit Ihrer primären Lösung in keiner Weise gefährdet werden?

Mit unserer Lösung erhalten Sie genau das: Maximalen Schutz für Ihre Anwendung bei gleichzeitigem Nutzen durch autorisierte Dritte – ganz ohne teure Lizenzkosten für eine Schattendatenbank.

Lassen Sie uns gemeinsam herausfinden, wie Sie Ihre Daten sicher und effizient nutzen können. Kontaktieren Sie uns – wir zeigen Ihnen, was möglich ist!
---------------------

Our second solution MIVO:
---------------------
MIVO – Program for a Tone Matching Instrument ist die smarte Lösung für Unternehmen, die bei Farbgenauigkeit keine Kompromisse machen. Die Software erkennt Farbabweichungen zwischen Mustern vollautomatisch, beschreibt sie verständlich und sorgt so für gleichbleibend hohe Produktqualität – schnell, visuell und präzise. Perfekt für alle, die Farbe zur Vertrauenssache machen.
-------------------------

Thanks,
Gerold

Target Market(s)

IT Professionals from any sector

Industry/Entity Type

Healthcare and other

Coding

Coded - Design and coding required

Number of Pages Required

1 page

Font styles to use
Sans Serif

Colors
0054AA
0677BA
7BADD7
CADEEF
E8F1F8
0094D4
00A9DD
6FCCEA
C7EBF8
E9F6FB
00AB8E
00BBA5
67D7C9
C6EFE9
E9F9F6

Requirements
Must have
• Please see description
Nice to have
• On the landing page the company should introduced with a small text (max 250 words) followed by a section with a short text to one of our products nearby a graphic visualising the architecture of the product. The menue should be on top and fixed during scrolling and consist of the menue items home, solutions, who are we and a contact button. There should be a footer for linking social media, rights and Impressum. Only as an idea not a must. The very first view on the landing page could also be the menue bar and below of it a transparent unsharp photo (e.g. datacenter, lines of code, both ;) with the company name in the center.
Should not have
• Please see description

```html
<!DOCTYPE html>
<html lang="en">
<head>
<meta charset="utf-8">
<title>QR.KA Horizon – Software Engineering &amp; IT</title>
<link href="https://fonts.googleapis.com/css2?family=Barlow:wght@400;500;600;700;800&display=swap" rel="stylesheet">
<style>
:root{
  --navy:#0b1f4a;
  --brand:#0054aa;
  --brand-2:#0677ba;
  --blue-band:#1e5cb3;
  --teal:#00ab8e;
  --teal-2:#00bba5;
  --ink:#1a1a1a;
  --muted:#555b66;
  --line:#e3e6ea;
  --dark:#0a1330;
  --footer:#262626;
  --white:#ffffff;
}
*{box-sizing:border-box;margin:0;padding:0}
html,body{width:1200px;height:3591px;overflow:hidden}
body{font-family:"Barlow",sans-serif;color:var(--ink);background:var(--white);position:relative}
.abs{position:absolute}

/* header */
.site-header{position:absolute;top:0;left:0;width:1200px;height:88px;background:var(--white);z-index:5}
.brand{position:absolute;left:105px;top:26px;display:flex;align-items:center;gap:12px}
.brand-dot{width:36px;height:36px;border-radius:50%;background:var(--brand)}
.brand-name{font-size:34px;font-weight:600;color:var(--navy);letter-spacing:.5px}
.main-nav{position:absolute;top:38px;left:504px;display:flex;gap:36px;font-size:14px;font-weight:600;letter-spacing:.4px}
.main-nav a{color:var(--ink);text-decoration:none}
.main-nav a.active{color:var(--brand)}
.login-btn{position:absolute;left:972px;top:21px;width:125px;height:43px;border-radius:22px;background:var(--brand);color:#fff;font-size:13px;font-weight:700;display:flex;align-items:center;justify-content:center;gap:7px}

/* hero */
.hero{position:absolute;top:88px;left:0;width:1200px;height:640px;background:radial-gradient(ellipse at 50% 30%,#2a5e7e 0%,#123a56 40%,#071a2c 100%)}
.hero-copy{position:absolute;top:105px;left:0;width:1200px;text-align:center;color:#fff}
.hero-kicker{font-size:36px;font-weight:400;letter-spacing:7px}
.hero-title{margin-top:18px;font-size:44px;line-height:49px;font-weight:500;letter-spacing:2px}
.hero-title b{font-weight:800}
.btn-light{display:inline-flex;align-items:center;justify-content:center;background:#fff;color:var(--ink);border-radius:24px;font-size:13px;font-weight:700}
.hero .btn-light{margin-top:24px;width:124px;height:45px}

/* products */
.products{position:absolute;top:630px;left:0;width:1200px;height:615px;background:linear-gradient(180deg,#1f5bb0,#1c56ab)}
.products-edge{position:absolute;top:625px;left:0}
.products-photo{position:absolute;left:119px;top:737px;width:442px;height:442px;border-radius:50%;background:radial-gradient(circle at 60% 40%,#e6d8c4,#b69a7c 55%,#5a4436)}
.products-copy{position:absolute;left:596px;top:746px;width:505px;color:#fff}
.products-copy h2{font-size:42px;font-weight:800;letter-spacing:.5px}
.products-copy p{margin-top:18px;font-size:17px;line-height:27.2px}
.products-copy .btn-light{margin-top:18px;width:126px;height:44px;color:var(--brand)}

/* solutions */
.section-title{position:absolute;left:0;width:1200px;text-align:center;font-size:46px;font-weight:800;color:var(--ink)}
.section-title span{color:var(--brand)}
.title-rule{position:absolute;height:2px;width:84px;background:var(--teal)}
.robot{position:absolute;left:255px;top:1438px;width:169px;height:264px;background:linear-gradient(180deg,#eef3f7,#c9d6e0)}
.sol-card{position:absolute;border:1px solid var(--line);background:#fff;text-align:center;color:var(--muted);font-size:16px;line-height:22px;padding:0 14px}
.sol-card.featured{background:linear-gradient(160deg,#00a79a,#07907f);color:#fff;border:none;box-shadow:0 8px 20px rgba(0,0,0,.12)}
.sol-icon{width:86px;height:86px;border-radius:50%;background:#eef1f4;margin:0 auto;display:flex;align-items:center;justify-content:center}
.featured .sol-icon{background:rgba(255,255,255,.18)}
.sol-card p{margin-top:16px}
.sol-arrow{margin-top:12px}

/* who we are */
.who{position:absolute;top:2058px;left:0;width:1200px;height:568px;background:linear-gradient(90deg,#0a1330 0%,#0c1a3d 50%,#0f2a4d 100%)}
.who-photo{position:absolute;left:570px;top:0;width:630px;height:568px;background:radial-gradient(ellipse at 45% 55%,#2b5b86 0%,#163457 45%,#0c1a3d 80%)}
.who-copy{position:absolute;left:105px;top:62px;width:450px;color:#fff}
.who-copy h2{font-size:46px;font-weight:800}
.who-copy h2 span{color:#2d79e0}
.who-copy .title-rule{position:static;margin-top:6px}
.who-copy p{margin-top:36px;font-size:17px;line-height:27.2px}
.btn-blue{display:inline-flex;align-items:center;justify-content:center;width:126px;height:44px;border-radius:24px;background:var(--brand);color:#fff;font-size:13px;font-weight:700;margin-top:22px}

/* blog */
.blog-card{position:absolute;top:2813px;width:300px;height:365px;border:1px solid var(--line);background:#fff}
.blog-img{height:168px}
.blog-body{padding:22px 16px 0}
.blog-body h3{font-size:17px;font-weight:600;letter-spacing:.2px}
.blog-body p{margin-top:10px;font-size:15.5px;line-height:21.5px;color:var(--muted)}
.blog-body a{display:inline-block;margin-top:8px;font-size:14px;font-weight:600;color:var(--brand);letter-spacing:.8px}
.slider-btn{position:absolute;top:2964px;width:48px;height:48px;border-radius:50%;display:flex;align-items:center;justify-content:center}
.slider-btn.prev{left:29px;border:1.5px solid #333}
.slider-btn.next{left:1125px;background:var(--ink)}

/* footer */
.site-footer{position:absolute;top:3270px;left:0;width:1200px;height:321px;background:var(--footer);color:#fff}
.footer-brand{position:absolute;top:38px;left:0;width:1200px;display:flex;justify-content:center;align-items:center;gap:12px}
.footer-brand .brand-dot{background:#fff}
.footer-brand .brand-name{color:#fff}
.footer-nav{position:absolute;top:128px;left:0;width:1200px;display:flex;justify-content:center;gap:44px;font-size:16px;letter-spacing:.6px}
.footer-nav .active{font-weight:700}
.socials{position:absolute;top:163px;left:0;width:1200px;display:flex;justify-content:center;gap:10px}
.social{width:48px;height:48px;border-radius:50%;border:1.5px solid #fff;display:flex;align-items:center;justify-content:center;font-size:11px;font-weight:600}
.social.active{background:var(--teal);border-color:var(--teal)}
.footer-rule{position:absolute;top:265px;left:105px;width:990px;height:1px;background:#4a4a4a}
.copyright{position:absolute;top:285px;left:0;width:1200px;text-align:center;font-size:13px}
</style>
</head>
<body>

<header class="site-header">
  <div class="brand"><span class="brand-dot"></span><span class="brand-name">QR.KA HORIZON</span></div>
  <nav class="main-nav">
    <a class="active" href="#">HOME</a>
    <a href="#">WHO WE ARE</a>
    <a href="#">OUR SOLUTIONS</a>
    <a href="#">CONTACT US</a>
  </nav>
  <div class="login-btn">
    <svg width="12" height="13" viewBox="0 0 12 13"><circle cx="6" cy="3.5" r="3" fill="#fff"/><path d="M0 13c0-4 2.7-6 6-6s6 2 6 6z" fill="#fff"/></svg>LOGIN
  </div>
</header>

<section class="hero" role="img" aria-label="Blurred data centre corridor with server racks">
  <div class="hero-copy">
    <div class="hero-kicker">QR.KA HORIZON</div>
    <h1 class="hero-title"><b>WHERE SOFTWARE MEETS</b><br><b>INFRASTRUCTURE</b> INNOVATIVE<br>ENGINEERING.SEAMLESS<br>IT INTEGRATION.</h1>
    <div class="btn-light">GET STARTED</div>
  </div>
</section>

<section class="products">
</section>
<svg class="products-edge" width="1200" height="110" viewBox="0 0 1200 110">
  <polygon points="0,97 600,6 1200,97 1200,110 0,110" fill="#1f5bb0"/>
  <polyline points="0,106 600,6 1200,106" fill="none" stroke="#fff" stroke-width="5"/>
</svg>
<div class="products-photo" role="img" aria-label="Person wearing a virtual reality headset"></div>
<div class="products-copy">
  <h2>OUR PRODUCTS</h2>
  <p>Lorem ipsum dolor sit amet, consectetur adipiscing elit, sed do eiusmod tempor incididunt ut labore et dolore magna aliqua. Ut enim ad minim veniam, quis nostrud exercitation ullamco laboris nisi ut aliquip ex ea commodo consequat. Duis aute irure dolor in reprehenderit in voluptate velit esse cillum dolore eu fugiat nulla pariatur. Excepteur sint occaecat cupidatat non proident, sunt in culpa qui officia deserunt mollit anim id est laborumDuis aute irure dolor in reprehenderit in voluptate velit esse cillum dolore eu fugiat nulla pariatur. Excepteur sint occaecat cupidatat</p>
  <div class="btn-light">READ MORE</div>
</div>

<h2 class="section-title" style="top:1320px">OUR <span>SOLUTIONS</span></h2>
<div class="title-rule" style="top:1383px;left:558px"></div>

<div class="robot" role="img" aria-label="Friendly white robot illustration giving a thumbs up"></div>

<div class="sol-card featured" style="left:424px;top:1438px;width:349px;height:270px;padding-top:28px">
  <div class="sol-icon"><svg width="44" height="40" viewBox="0 0 44 40" fill="none" stroke="#fff" stroke-width="2"><rect x="2" y="2" width="40" height="28" rx="2"/><path d="M16 38h12M22 30v8"/><circle cx="22" cy="16" r="6"/></svg></div>
  <p>Lorem ipsum dolor sit amet, consectetur adipiscing elit, sed do eiusmod tempor cididunt ut labore etaliqua.</p>
  <div class="sol-arrow"><svg width="26" height="20" viewBox="0 0 26 20" fill="none" stroke="#fff" stroke-width="3"><path d="M2 10h21M15 2l8 8-8 8"/></svg></div>
</div>
<div class="sol-card" style="left:773px;top:1443px;width:324px;height:259px;padding-top:22px">
  <div class="sol-icon"><svg width="44" height="40" viewBox="0 0 44 40" fill="none" stroke="#1d4fa3" stroke-width="2"><rect x="2" y="6" width="40" height="24" rx="2"/><path d="M16 38h12M22 30v8M12 22l6-7 6 5 8-9"/></svg></div>
  <p>Lorem ipsum dolor sit amet, consectetur adipiscing elit, sed do eiusmod tempor cididunt ut labore etaliqua.</p>
  <div class="sol-arrow"><svg width="22" height="18" viewBox="0 0 22 18" fill="none" stroke="#111" stroke-width="3"><path d="M1 9h18M12 2l7 7-7 7"/></svg></div>
</div>
<div class="sol-card" style="left:101px;top:1702px;width:334px;height:260px;padding-top:22px">
  <div class="sol-icon"><svg width="44" height="40" viewBox="0 0 44 40" fill="none" stroke="#1d4fa3" stroke-width="2"><ellipse cx="22" cy="7" rx="12" ry="4"/><path d="M10 7v26c0 2 5 4 12 4s12-2 12-4V7M10 20c0 2 5 4 12 4s12-2 12-4"/></svg></div>
  <p>Lorem ipsum dolor sit amet, consectetur adipiscing elit, sed do eiusmod tempor cididunt ut labore etaliqua.</p>
  <div class="sol-arrow"><svg width="22" height="18" viewBox="0 0 22 18" fill="none" stroke="#111" stroke-width="3"><path d="M1 9h18M12 2l7 7-7 7"/></svg></div>
</div>
<div class="sol-card" style="left:435px;top:1702px;width:331px;height:260px;padding-top:22px">
  <div class="sol-icon"><svg width="44" height="40" viewBox="0 0 44 40" fill="none" stroke="#1d4fa3" stroke-width="2"><circle cx="22" cy="13" r="7"/><path d="M8 38c0-8 6-13 14-13s14 5 14 13"/></svg></div>
  <p>Lorem ipsum dolor sit amet, consectetur adipiscing elit, sed do eiusmod tempor cididunt ut labore etaliqua.</p>
  <div class="sol-arrow"><svg width="22" height="18" viewBox="0 0 22 18" fill="none" stroke="#111" stroke-width="3"><path d="M1 9h18M12 2l7 7-7 7"/></svg></div>
</div>
<div class="sol-card" style="left:766px;top:1702px;width:331px;height:260px;padding-top:22px">
  <div class="sol-icon"><svg width="44" height="40" viewBox="0 0 44 40" fill="none" stroke="#1d4fa3" stroke-width="2"><circle cx="26" cy="13" r="8"/><circle cx="26" cy="13" r="3"/><path d="M2 30h10l8 4h10l10-6"/></svg></div>
  <p>Lorem ipsum dolor sit amet, consectetur adipiscing elit, sed do eiusmod tempor cididunt ut labore etaliqua.</p>
  <div class="sol-arrow"><svg width="22" height="18" viewBox="0 0 22 18" fill="none" stroke="#111" stroke-width="3"><path d="M1 9h18M12 2l7 7-7 7"/></svg></div>
</div>

<section class="who">
  <div class="who-photo" role="img" aria-label="Developer working on a laptop surrounded by glowing data"></div>
  <div class="who-copy">
    <h2>WHO <span>WE ARE</span></h2>
    <div class="title-rule"></div>
    <p>Lorem ipsum dolor sit amet, consectetur adipiscing elit, sed do eiusmod tempor incididunt ut labore et dolore magna iqua. Ut enim ad minim veniam, quis nostrud exercitation ullamco laboris nisi ut aliquip ex ea commodo consequat. Duis aute rure dolor in reprehenderit in voluptate velit esse cillum olore eu fugiat nulla pariatur. Excepteur sint occaecat cupidatat on proident, sunt in culpa qui officia deserunt mollit anim id est laborumDuis aute irure dolor in reprehederit in voluptate velit esse cillum dolore eu fugiat nulla pariatur. Excepteur sint aecat cupidatat occaecat cupidatat.</p>
    <div class="btn-blue">READ MORE</div>
  </div>
</section>

<h2 class="section-title" style="top:2705px">OUR <span>LATEST BLOG</span></h2>
<div class="title-rule" style="top:2767px;left:558px"></div>

<div class="slider-btn prev"><svg width="10" height="16" viewBox="0 0 10 16" fill="none" stroke="#222" stroke-width="2"><path d="M8 2L2 8l6 6"/></svg></div>
<div class="slider-btn next"><svg width="10" height="16" viewBox="0 0 10 16" fill="none" stroke="#fff" stroke-width="2"><path d="M2 2l6 6-6 6"/></svg></div>

<article class="blog-card" style="left:104px">
  <div class="blog-img" role="img" aria-label="Hands typing on a backlit keyboard with code on screen" style="background:linear-gradient(135deg,#0e2c4a,#1f6a8f 55%,#c4672a)"></div>
  <div class="blog-body"><h3>LOREM IPSUM DOLOR SIT AMET</h3><p>Lorem ipsum dolor sit amet, etu ngelit, sed do iumod por incididunt t labore et ore agna aliquasit amet, netu incidunt ut incididunt t labore.</p><a href="#">READ MORE</a></div>
</article>
<article class="blog-card" style="left:449px">
  <div class="blog-img" role="img" aria-label="Developer thinking at a desk with monitors" style="background:linear-gradient(135deg,#6b5a48,#a8a6a1 55%,#3e4a57)"></div>
  <div class="blog-body"><h3>LOREM IPSUM DOLOR SIT AMET</h3><p>Lorem ipsum dolor sit amet, etu ngelit, sed do iumod por incididunt t labore et ore agna aliquasit amet, netu incidunt ut incididunt t labore.</p><a href="#">READ MORE</a></div>
</article>
<article class="blog-card" style="left:795px">
  <div class="blog-img" role="img" aria-label="Laptop screen showing lines of code" style="background:linear-gradient(135deg,#0b1b33,#1d4f7c 55%,#0a1426)"></div>
  <div class="blog-body"><h3>LOREM IPSUM DOLOR SIT AMET</h3><p>Lorem ipsum dolor sit amet, etu ngelit, sed do iumod por incididunt t labore et ore agna aliquasit amet, netu incidunt ut incididunt t labore.</p><a href="#">READ MORE</a></div>
</article>

<footer class="site-footer">
  <div class="footer-brand"><span class="brand-dot"></span><span class="brand-name">QR.KA HORIZON</span></div>
  <nav class="footer-nav"><span class="active">HOME</span><span>WHO WE ARE</span><span>OUR SOLUTIONS</span><span>CONTACT US</span></nav>
  <div class="socials"><span class="social active">Lynk</span><span class="social">Fabo</span><span class="social">Pixo</span></div>
  <div class="footer-rule"></div>
  <div class="copyright">© 2025 QR.KA Horizon. All Rights Reserved.</div>
</footer>

</body>
</html>
```